Counseling Practice Business Card

I need a professional looking business card incorporating my new logo that was just completed. Card needs to incorporate my name and title, description of my specialty, my address, my phone number, my fax number, my email and my website URL. I need to be able to choose design on/with different paper colors and textures.
I do not have a lot of business card ideas so I am open to anything but I want bold,sharp, clear card without additional designs other than my logo (see attached file info). I am open to different color backgrounds or paper colors including black. I do not like traditional brackets around area codes in phone number or dashes between numbers in phone number. Am open to other ways of presenting including periods between numbers as appropriate. I do not know enough to know what I like yet but I want card to coordinate and work together with my logo. My practice emphasizes natural mental health interventions so any use of color (with background paper color or the blue and green in my logo) that elicits nature is nice. In addition to black, any natural brown or wood looking background might be desirable also. Most of the offerings so far look very similar and boring.

Target Market(s)

Potential therapy clients and other professionals

Contact Information for Business Card

Card information:
Gerald M. Whitcombe, Ph.D.
Licensed Clinical Psychologist
Integrative Health Coach
4812 Marlowe Ridge Blvd SE
Suite 310
Duluth, GA 30096
(770) 415-2983 phone
(770) 581-4096 fax
drgeraldwhitcombe@quillmarsh.net
brightfernwellness.net

Font styles to use
Serif
Sans Serif
Other font styles liked:
• anything that you think looks crisp, clear and easily readable

Requirements
Must have
• Any color used should coordinate with my logo design (see attached files).
• Card should be printed horizontally so top and bottom are longest sides of rectangle.
• Background color or paper color should complement and highlight logo. Do not like a white background. black, grey, brown or any color my logo would blend well with.
Nice to have
• I would like designer to utilize color to highlight letters/name or phone-fax-web symbols.
• Bottom edge of card could be highlighted if appropriate to an idea.
Should not have
• I would NOT want the card to have a pure white background at all.
• No clear cards.
• Cards should be oriented with long sides on bottom and top, NOT sides. DO NOT LIKE THIS THIN TALL ORIENTATION.

```html
<!DOCTYPE html>
<html lang="en">
<head>
<meta charset="utf-8">
<title>Brightfern Wellness – Business Card</title>
<link rel="stylesheet" href="https://fonts.googleapis.com/css2?family=Source+Serif+4:wght@400;600;700&display=swap">
<style>
  :root {
    --forest: #006837;
    --sky: #2673b7;
    --paper: #ffffff;
    --ink: #111111;
    --stage: #ffffff;
  }
  * { margin: 0; padding: 0; box-sizing: border-box; }
  html, body {
    width: 1000px; height: 1200px; overflow: hidden;
    background: var(--stage);
    font-family: "Source Serif 4", Georgia, serif;
  }
  .card {
    position: absolute; left: 60px; top: 338px;
    width: 898px; height: 539px; overflow: hidden;
  }
  .card-bg { position: absolute; inset: 0; }
  .brand {
    position: absolute; left: 60px; top: 112px; width: 320px;
    text-align: center; color: var(--sky); font-weight: 600;
  }
  .brand-name { font-size: 56px; line-height: 1; display: block; }
  .brand-sub { font-size: 21px; letter-spacing: 9px; display: block; margin-top: 6px; }
  .address {
    position: absolute; left: 62px; top: 334px;
    font-size: 24px; font-weight: 600; line-height: 32px; color: var(--ink);
  }
  .name {
    position: absolute; right: 57px; top: 84px;
    font-size: 26px; font-weight: 400; color: var(--paper); letter-spacing: .3px;
  }
  .name strong { font-weight: 700; }
  .name-rule {
    position: absolute; left: 442px; right: 0; top: 122px;
    height: 3px; background: var(--paper);
  }
  .title {
    position: absolute; right: 57px; top: 145px;
    text-align: right; font-size: 24px; line-height: 33px; color: var(--paper);
  }
  .contacts {
    position: absolute; right: 60px; top: 320px;
    list-style: none; color: var(--paper); font-size: 23px; font-weight: 600;
  }
  .contacts li {
    display: flex; justify-content: flex-end; align-items: center;
    height: 40px; gap: 16px;
  }
  .contacts svg { width: 26px; height: 26px; flex: none; }
</style>
</head>
<body>
<div class="card">
  <svg class="card-bg" width="898" height="539" viewBox="0 0 898 539" aria-hidden="true">
    <rect x="0" y="0" width="898" height="265" fill="var(--forest)"/>
    <rect x="0" y="265" width="898" height="274" fill="var(--sky)"/>
    <ellipse cx="100" cy="267" rx="356" ry="362" fill="#ffffff" fill-opacity=".38"/>
    <ellipse cx="100" cy="267" rx="340" ry="346" fill="var(--paper)"/>
  </svg>

  <div class="brand">
    <span class="brand-name">Brightfern</span>
    <span class="brand-sub">WELLNESS</span>
  </div>

  <p class="address">4812 Marlowe Ridge Blvd SE,<br>Suite 310, Duluth,<br>GA 30096</p>

  <p class="name"><strong>GERALD M.</strong> WHITCOMBE, PH.D.</p>
  <div class="name-rule"></div>
  <p class="title">Licensed Clinical Psycologist/<br>Integrative Health Coach</p>

  <ul class="contacts">
    <li>P: 770 415 2983
      <svg viewBox="0 0 26 26" aria-label="phone"><rect x="8" y="3" width="10" height="20" rx="2.5" fill="none" stroke="#fff" stroke-width="2"/><rect x="10" y="6" width="6" height="6" fill="#fff"/></svg>
    </li>
    <li>F: 770 581 4096
      <svg viewBox="0 0 26 26" aria-label="fax"><rect x="3" y="4" width="7" height="18" rx="1.5" fill="none" stroke="#fff" stroke-width="2"/><rect x="10" y="11" width="13" height="11" fill="none" stroke="#fff" stroke-width="2"/><path d="M10 11l6.5 6 6.5-6" fill="none" stroke="#fff" stroke-width="2"/></svg>
    </li>
    <li>brightfernwellness.net
      <svg viewBox="0 0 26 26" aria-label="website"><circle cx="13" cy="13" r="10" fill="none" stroke="#fff" stroke-width="2"/><ellipse cx="13" cy="13" rx="4.5" ry="10" fill="none" stroke="#fff" stroke-width="2"/><path d="M3 13h20M5 8h16M5 18h16" stroke="#fff" stroke-width="1.6"/></svg>
    </li>
    <li>drgeraldwhitcombe@quillmarsh.net
      <svg viewBox="0 0 26 26" aria-label="email"><rect x="2" y="6" width="22" height="15" fill="none" stroke="#fff" stroke-width="2"/><path d="M2 6l11 9 11-9M2 21l8-7M24 21l-8-7" fill="none" stroke="#fff" stroke-width="2"/></svg>
    </li>
  </ul>
</div>
</body>
</html>
```